Business Card Design

Carl Brenton Insurance Agency, an Independent Insurance Agency which was stated on Pine Street in Laplace, Louisiana on 1961 and has grown the six locations throughout South Louisiana. We sell personal (auto Homeowners flood, liability) and commercial insurance (commercial property, general liability, workers compensation, commercial auto). I am looking for a double sided card with list the five remaining locations on the back or maybe even a folded four sided card. Our home office is a two story building with a green roof. I have had a logo designed which I have attached. Open for revisions but would like to stay with in the same green roof over an M. I have attached the logo but can not tell if I was uploaded.

Target Market(s)

Individual and commercial insurance buyers. Upper income and business owners

Industry/Entity Type

Insurance

Requirements
Must have
• Must have similar logo as uploaded. Green roof over M or something similar. List all location address and phone numbers.

Employee name, office phone number; direct phone line; email address and website list all locations on card. Very Similar colors to current logo.
Nice to have
• Possible folded card with double sided print

```html
<!DOCTYPE html>
<html lang="en">
<head>
<meta charset="utf-8">
<title>Carl Brenton Insurance Agency – Business Cards</title>
<link href="https://fonts.googleapis.com/css2?family=Open+Sans:wght@400;600;700;800&display=swap" rel="stylesheet">
<style>
  :root {
    --green: #1f6b4f;
    --green-dark: #16543d;
    --blue: #2a63ad;
    --grey: #6e6e6e;
    --paper: #ffffff;
    --backdrop: #e9e6e1;
  }
  * { box-sizing: border-box; margin: 0; padding: 0; }
  html, body {
    width: 1200px; height: 1023px; overflow: hidden;
    background: var(--backdrop);
    font-family: "Open Sans", Arial, sans-serif;
  }
  .canvas { position: relative; width: 1200px; height: 1023px; }

  .card {
    position: absolute;
    width: 700px; height: 400px;
    background: var(--paper);
    overflow: hidden;
    box-shadow: 0 10px 28px rgba(0,0,0,.22);
  }
  .card--front { left: 70px; top: 70px; }
  .card--back  { left: 430px; top: 550px; }

  /* front */
  .front-shapes { position: absolute; inset: 0; }
  .brand {
    position: absolute; left: 72px; top: 92px;
    display: flex; align-items: center; gap: 12px;
  }
  .brand__mark { width: 22px; height: 22px; background: var(--green); flex: none; }
  .brand__name {
    font-weight: 800; color: var(--green-dark);
    font-size: 19px; line-height: 1.05; text-transform: uppercase;
  }
  .brand__tagline {
    position: absolute; left: 106px; top: 146px;
    font-size: 11px; font-weight: 600; color: var(--grey);
  }
  .person { position: absolute; left: 72px; top: 190px; }
  .person__name { font-size: 24px; font-weight: 700; color: var(--green); }
  .person__title { font-size: 16px; color: var(--grey); }

  .contacts {
    position: absolute; left: 72px; top: 282px;
    list-style: none; color: #fff; font-size: 15px; line-height: 23px;
  }
  .contacts li { display: flex; align-items: center; gap: 10px; }
  .contacts svg { width: 14px; height: 14px; flex: none; }

  .address {
    position: absolute; left: 420px; top: 150px;
    color: #fff; font-size: 15px; line-height: 22px; font-style: normal;
  }
  .address__label { font-weight: 700; }

  /* back */
  .back-brand {
    position: absolute; left: 70px; top: 80px;
    display: flex; align-items: center; gap: 18px;
  }
  .back-brand__mark { width: 48px; height: 48px; background: var(--green); flex: none; }
  .back-brand__name {
    font-weight: 800; color: var(--green-dark);
    font-size: 40px; line-height: 1.05; text-transform: uppercase;
  }
  .back-tagline {
    position: absolute; left: 136px; top: 200px;
    font-size: 26px; font-weight: 600; color: var(--grey);
  }
  .back-invite {
    position: absolute; left: 136px; top: 240px;
    font-size: 17px; color: var(--blue);
  }
  .locations {
    position: absolute; left: 136px; top: 282px;
    list-style: none; display: flex; gap: 10px; white-space: nowrap;
    font-size: 14px; font-weight: 700; letter-spacing: 1.5px; color: var(--green-dark);
  }
  .locations li + li::before { content: "•"; margin-right: 10px; }
</style>
</head>
<body>
<main class="canvas">

  <section class="card card--front" aria-label="Business card front">
    <svg class="front-shapes" width="700" height="400" viewBox="0 0 700 400" aria-hidden="true">
      <defs>
        <linearGradient id="sheen" x1="0" y1="0" x2="0" y2="1">
          <stop offset="0" stop-color="#fff" stop-opacity=".08"/>
          <stop offset="1" stop-color="#000" stop-opacity=".08"/>
        </linearGradient>
      </defs>
      <rect x="380" y="0" width="320" height="74" fill="var(--green)"/>
      <rect x="400" y="96" width="300" height="304" fill="var(--green)"/>
      <rect x="0" y="262" width="700" height="138" fill="var(--green)"/>
      <rect x="0" y="262" width="700" height="138" fill="url(#sheen)"/>
    </svg>

    <div class="brand">
      <span class="brand__mark"></span>
      <span class="brand__name">Carl Brenton<br>Insurance Agency</span>
    </div>
    <p class="brand__tagline">Serving Pine Street Since 1961</p>

    <div class="person">
      <p class="person__name">Mara Delcour</p>
      <p class="person__title">Manager</p>
    </div>

    <ul class="contacts">
      <li>
        <svg viewBox="0 0 14 14"><path d="M3 1h3l1 3-2 1.5a8 8 0 0 0 3.5 3.5L10 7l3 1v3a2 2 0 0 1-2 2A11 11 0 0 1 1 3a2 2 0 0 1 2-2z" fill="#fff"/></svg>
        225-555-0142
      </li>
      <li>
        <svg viewBox="0 0 14 14"><rect x="1.5" y="1.5" width="11" height="11" fill="none" stroke="#fff" stroke-width="1.4"/></svg>
        225-555-0197
      </li>
      <li>
        <svg viewBox="0 0 14 14"><rect x="1" y="3" width="12" height="8" fill="none" stroke="#fff" stroke-width="1.4"/><path d="M1 3l6 5 6-5" fill="none" stroke="#fff" stroke-width="1.4"/></svg>
        mara.delcour@carlbrenton.com
      </li>
      <li>
        <svg viewBox="0 0 14 14"><rect x="1.5" y="2" width="11" height="8" fill="none" stroke="#fff" stroke-width="1.4"/><path d="M5 12h4" stroke="#fff" stroke-width="1.4"/></svg>
        www.carlbrentoninsurance.com
      </li>
    </ul>

    <address class="address">
      <span class="address__label">Address :</span><br>
      2240 River Road, Suite B<br>
      Riverton LA 70555
    </address>
  </section>

  <section class="card card--back" aria-label="Business card back">
    <div class="back-brand">
      <span class="back-brand__mark"></span>
      <span class="back-brand__name">Carl Brenton<br>Insurance Agency</span>
    </div>
    <p class="back-tagline">Serving Pine Street Since 1961</p>
    <p class="back-invite">Visit one of our 6 convenient locations</p>
    <ul class="locations">
      <li>Ashford</li>
      <li>Belmont</li>
      <li>Cedar Bend</li>
      <li>Dalton</li>
      <li>Fairview</li>
    </ul>
  </section>

</main>
</body>
</html>
```